Telecommunications/Power civil contractor needs business card design

Were a new telecommunications/power underground civil contractor that is looking for a new business card design. Our company colours are silver or grey and orange. Feel free to use the white background logo or the black background logo.

Target Market(s)

Local contractors, utility companies, private sector mining/energy companies, developers.

Industry/Entity Type

Telecommunications

Contact Information for Business Card

Each card will need the following info:
Persons name:
Title:
E-mail:
Phone number:
Shop Address:
Mailing Address:

Requirements
Must have
• Each card will need the following info:
• Persons name:
• Title:
• E-mail:
• Phone number:
• Shop Address:
• Mailing Address:

```html
<!DOCTYPE html>
<html lang="en">
<head>
<meta charset="utf-8">
<title>Trenchline Civil Inc — Business Card</title>
<link rel="stylesheet" href="https://fonts.googleapis.com/css2?family=Lato:wght@400;700;900&family=Arimo:wght@400&display=swap">
<style>
  :root {
    --backdrop: #2b2b2b;
    --card: #f7f7f7;
    --card-edge: #e4e4e4;
    --ink: #5a5a5a;
    --ink-soft: #6e6e6e;
    --accent: #e0541c;
    --rule: #7a7a7a;
    --icon: #6f6f6f;
  }
  html, body {
    margin: 0;
    width: 1200px;
    height: 997px;
    overflow: hidden;
    background: var(--backdrop);
  }
  .stage {
    position: relative;
    width: 1200px;
    height: 997px;
  }
  .business-card {
    position: absolute;
    left: 180px;
    top: 258px;
    width: 840px;
    height: 480px;
    background: linear-gradient(160deg, #ffffff 0%, var(--card) 60%, var(--card-edge) 100%);
    border-radius: 28px;
    box-shadow: 0 18px 40px rgba(0,0,0,0.55);
    font-family: "Arimo", Arial, sans-serif;
  }
  .brand {
    position: absolute;
    right: 72px;
    top: 62px;
    display: flex;
    align-items: center;
    gap: 14px;
  }
  .brand-dot {
    width: 34px;
    height: 34px;
    border-radius: 50%;
    background: var(--accent);
  }
  .brand-name {
    font-family: "Lato", sans-serif;
    font-weight: 900;
    font-size: 30px;
    letter-spacing: 1px;
    color: var(--accent);
  }
  .holder {
    position: absolute;
    left: 72px;
    top: 212px;
    right: 72px;
  }
  .holder-row {
    display: flex;
    align-items: flex-end;
    gap: 18px;
  }
  .holder-name {
    font-family: "Lato", sans-serif;
    font-weight: 900;
    font-size: 34px;
    color: var(--ink);
    white-space: nowrap;
    line-height: 1;
  }
  .holder-rule {
    flex: 1;
    height: 2px;
    background: var(--rule);
    margin-bottom: 4px;
  }
  .holder-title {
    margin-top: 8px;
    font-family: "Lato", sans-serif;
    font-weight: 700;
    font-size: 19px;
    letter-spacing: 0.5px;
    color: var(--accent);
    text-transform: uppercase;
  }
  .contact-list {
    position: absolute;
    left: 72px;
    top: 320px;
    margin: 0;
    padding: 0;
    list-style: none;
  }
  .contact-item {
    display: flex;
    align-items: flex-start;
    gap: 16px;
    font-size: 21px;
    line-height: 28px;
    color: var(--ink-soft);
    margin-bottom: 10px;
  }
  .contact-icon {
    flex: none;
    width: 24px;
    height: 24px;
    margin-top: 2px;
  }
  .email {
    position: absolute;
    right: 72px;
    top: 322px;
    font-size: 22px;
    font-weight: 400;
    color: var(--accent);
  }
</style>
</head>
<body>
<main class="stage">
  <section class="business-card">
    <div class="brand">
      <span class="brand-dot"></span>
      <span class="brand-name">TRENCHLINE CIVIL INC</span>
    </div>

    <div class="holder">
      <div class="holder-row">
        <span class="holder-name">Maren Holloway</span>
        <span class="holder-rule"></span>
      </div>
      <div class="holder-title">Founder &amp; CEO</div>
    </div>

    <ul class="contact-list">
      <li class="contact-item">
        <svg class="contact-icon" viewBox="0 0 24 24" aria-hidden="true">
          <circle cx="12" cy="12" r="12" fill="var(--icon)"/>
          <path d="M8 6.5l2.2 0 1 3-1.5 1.2a7 7 0 0 0 3.6 3.6l1.2-1.5 3 1 0 2.2c0 .6-.5 1-1 1A10 10 0 0 1 7 7.5c0-.5.4-1 1-1z" fill="#fff"/>
        </svg>
        <span>+1 (555) 310-4826</span>
      </li>
      <li class="contact-item">
        <svg class="contact-icon" viewBox="0 0 24 24" aria-hidden="true">
          <circle cx="12" cy="12" r="12" fill="var(--icon)"/>
          <path d="M12 6l6 5.2h-1.8V17h-3v-3.4h-2.4V17h-3v-5.8H6z" fill="#fff"/>
        </svg>
        <span>Unit 42, Sector 7, Ridgefield</span>
      </li>
      <li class="contact-item">
        <svg class="contact-icon" viewBox="0 0 24 24" aria-hidden="true">
          <circle cx="12" cy="12" r="12" fill="var(--icon)"/>
          <path d="M12 5.5a4.2 4.2 0 0 0-4.2 4.2c0 3.1 4.2 8 4.2 8s4.2-4.9 4.2-8A4.2 4.2 0 0 0 12 5.5zm0 5.8a1.6 1.6 0 1 1 0-3.2 1.6 1.6 0 0 1 0 3.2z" fill="#fff"/>
        </svg>
        <span>18 Alder Creek Road, 2nd Floor,<br>Lakeport, CT 06099</span>
      </li>
    </ul>

    <div class="email">hello@trenchlinecivil.com</div>
  </section>
</main>
</body>
</html>
```